We are a recruitment company based in Norwich/Cambridge England.
I have included our company logo which we want to remain the same.

What we are looking for is a new creative Business card which will really stand out!!

Contact Information for Business Card

Harriet Dunmore
email: Harriet@plavex.co.uk
Address: Brackwell House
Fenmoor Enterprise Park
Partridge Way
Norwich
QB9 3KX
Tel:01632 960418

```html
<!DOCTYPE html>
<html lang="en">
<head>
<meta charset="utf-8">
<title>Plavex Business Card</title>
<link rel="stylesheet" href="https://fonts.googleapis.com/css2?family=Montserrat:wght@400;500;600&display=swap">
<style>
  :root {
    --bg: #151515;
    --card: #262626;
    --card-edge: #2e2e2e;
    --green: #7dc242;
    --white: #f2f2f2;
    --grey: #d8d8d8;
  }
  * { box-sizing: border-box; margin: 0; padding: 0; }
  html, body {
    width: 1200px; height: 900px; overflow: hidden;
    background: var(--bg);
    font-family: "Montserrat", sans-serif;
  }
  .stage {
    width: 1200px; height: 900px;
    display: flex; flex-direction: column; align-items: center; justify-content: center;
    gap: 40px;
  }
  .card {
    position: relative;
    width: 620px; height: 354px;
    background: linear-gradient(135deg, var(--card) 0%, var(--card-edge) 100%);
    border-bottom: 5px solid var(--green);
    box-shadow: 0 14px 30px rgba(0,0,0,0.55);
    overflow: hidden;
  }
  .brand { display: flex; align-items: center; gap: 14px; }
  .brand-dot {
    width: 54px; height: 54px; border-radius: 50%;
    background: var(--green);
  }
  .brand-text { display: flex; flex-direction: column; }
  .brand-name {
    font-size: 46px; font-weight: 600; color: var(--white);
    line-height: 1; letter-spacing: -0.5px;
  }
  .brand-tagline {
    font-size: 9.5px; font-weight: 500; color: var(--white);
    letter-spacing: 3.2px; margin-top: 4px;
  }

  /* front */
  .card-front .brand {
    position: absolute; left: 50%; top: 128px; transform: translateX(-50%);
  }
  .card-front .web {
    position: absolute; left: 0; right: 0; bottom: 26px;
    text-align: center; font-size: 15px; letter-spacing: 1px; color: var(--white);
  }
  .accent { color: var(--green); }

  /* back */
  .card-back .brand { position: absolute; left: 44px; top: 128px; }
  .card-back .brand-dot { width: 46px; height: 46px; }
  .card-back .brand-name { font-size: 40px; }
  .card-back .brand-tagline { font-size: 8.5px; letter-spacing: 2.8px; }
  .divider {
    position: absolute; left: 318px; top: 78px;
    width: 2px; height: 190px; background: var(--green);
  }
  .contact { position: absolute; left: 346px; top: 80px; color: var(--white); }
  .contact-name { font-size: 24px; font-weight: 600; color: var(--green); letter-spacing: 0.5px; }
  .contact-role { font-size: 15px; letter-spacing: 1px; margin-bottom: 14px; }
  .contact-address { font-size: 14px; line-height: 1.45; letter-spacing: 0.6px; margin-bottom: 10px; }
  .contact-line {
    display: flex; align-items: center; gap: 10px;
    font-size: 14px; letter-spacing: 0.6px; line-height: 1.75;
  }
  .contact-line svg { width: 12px; height: 12px; flex: none; }
</style>
</head>
<body>
<main class="stage">
  <section class="card card-front">
    <div class="brand">
      <span class="brand-dot"></span>
      <div class="brand-text">
        <span class="brand-name">Plavex</span>
        <span class="brand-tagline">Technology Recruitment</span>
      </div>
    </div>
    <p class="web">www.<span class="accent">plavex</span>.co.uk</p>
  </section>

  <section class="card card-back">
    <div class="brand">
      <span class="brand-dot"></span>
      <div class="brand-text">
        <span class="brand-name">Plavex</span>
        <span class="brand-tagline">Technology Recruitment</span>
      </div>
    </div>
    <span class="divider"></span>
    <div class="contact">
      <h1 class="contact-name">Harriet Dunmore</h1>
      <p class="contact-role">Founder</p>
      <p class="contact-address">Brackwell House, Partridge Way<br>QB9 3KX Norwich</p>
      <p class="contact-line">
        <svg viewBox="0 0 12 12" aria-hidden="true"><path d="M2.5 1 L4.5 1 L5 3.5 L3.8 4.4 Q4.8 6.8 7.4 8.1 L8.4 7 L11 7.5 L11 9.5 Q10.5 11 9 11 Q1 9.5 1 2.8 Q1 1 2.5 1 Z" fill="#7dc242"/></svg>
        01632 960418
      </p>
      <p class="contact-line">
        <svg viewBox="0 0 12 12" aria-hidden="true"><rect x="1" y="2.5" width="10" height="7" fill="none" stroke="#7dc242" stroke-width="1"/><path d="M1 2.5 L6 6.5 L11 2.5" fill="none" stroke="#7dc242" stroke-width="1"/></svg>
        Harriet@plavex.co.uk
      </p>
      <p class="contact-line">
        <svg viewBox="0 0 12 12" aria-hidden="true"><circle cx="6" cy="6" r="5" fill="none" stroke="#7dc242"/><ellipse cx="6" cy="6" rx="2.2" ry="5" fill="none" stroke="#7dc242"/><path d="M1 6 H11" stroke="#7dc242"/></svg>
        www.<span class="accent">plavex</span>.co.uk
      </p>
    </div>
  </section>
</main>
</body>
</html>
```